Corporate Business Card

Very professional, Modern, Not to busy, include phone address email, website
(253) 617-4930, 18761 52nd Avenue S, Marrow Falls, OR 98047, martin@plumlinegroup.com, varkoworks.com

Target Market(s)

Manufacturing

Industry/Entity Type

Aero, machining, manufacturing, Off road racing

Contact Information for Business Card

Phone, address email, website

```html
<!DOCTYPE html>
<html lang="en">
<head>
<meta charset="utf-8">
<title>Varko Works – Business Card</title>
<link href="https://fonts.googleapis.com/css2?family=Open+Sans:wght@400;600&family=Titillium+Web:wght@600;700&display=swap" rel="stylesheet">
<style>
  :root {
    --navy: #17356f;
    --red: #d9232e;
    --white: #ffffff;
    --ink: #3a3a3a;
    --backdrop: #1d1e20;
  }
  * { margin: 0; padding: 0; box-sizing: border-box; }
  html, body { width: 1200px; height: 786px; overflow: hidden; background: var(--backdrop); }
  .canvas { position: relative; width: 1200px; height: 786px; }

  .card {
    position: absolute;
    width: 520px; height: 297px;
    border-radius: 16px;
    overflow: hidden;
  }

  /* Back side */
  .card-back { left: 50px; top: 80px; background: var(--navy); }
  .card-back .brand {
    position: absolute; left: 0; right: 0; top: 104px;
    text-align: center;
    font-family: "Titillium Web", sans-serif; font-weight: 700;
    font-size: 54px; letter-spacing: 1px; line-height: 1;
    color: var(--white);
  }
  .card-back .rule {
    position: absolute; left: 130px; top: 178px;
    width: 260px; height: 2px; background: var(--white);
  }

  /* Front side */
  .card-front { left: 630px; top: 410px; background: var(--white); }
  .card-front .brand {
    position: absolute; right: 36px; top: 34px;
    font-family: "Titillium Web", sans-serif; font-weight: 700;
    font-size: 32px; line-height: 1; color: var(--navy);
  }
  .person { position: absolute; left: 38px; top: 100px; }
  .person .name {
    font-family: "Titillium Web", sans-serif; font-weight: 700;
    font-size: 26px; line-height: 1; letter-spacing: .5px;
    color: var(--navy); text-transform: uppercase;
  }
  .person .role {
    font-family: "Open Sans", sans-serif; font-size: 13px;
    color: var(--red); margin-top: 3px;
  }
  .contacts { list-style: none; margin-top: 10px; }
  .contacts li {
    display: flex; align-items: center; gap: 8px;
    font-family: "Open Sans", sans-serif; font-size: 12.5px;
    color: var(--ink); line-height: 19px;
  }
  .contacts svg { width: 11px; height: 11px; fill: var(--navy); flex: none; }
  .divider {
    position: absolute; left: 38px; top: 222px;
    width: 350px; height: 1.5px; background: var(--navy);
  }
  .address {
    position: absolute; left: 38px; top: 230px;
    font-family: "Open Sans", sans-serif; font-size: 12.5px; color: var(--ink);
  }
  .edge-band { position: absolute; left: 0; bottom: 0; width: 520px; height: 20px; }
</style>
</head>
<body>
<main class="canvas">

  <section class="card card-back" aria-label="Card back">
    <div class="brand">Varko Works</div>
    <div class="rule"></div>
  </section>

  <section class="card card-front" aria-label="Card front">
    <div class="brand">Varko Works</div>

    <div class="person">
      <h1 class="name">Dale Whitcomb</h1>
      <p class="role">Managing Director</p>
      <ul class="contacts">
        <li>
          <svg viewBox="0 0 24 24"><path d="M6.6 10.8a15.1 15.1 0 0 0 6.6 6.6l2.2-2.2c.3-.3.7-.4 1-.2 1.1.4 2.3.6 3.6.6.6 0 1 .4 1 1V20c0 .6-.4 1-1 1A17 17 0 0 1 3 4c0-.6.4-1 1-1h3.5c.6 0 1 .4 1 1 0 1.3.2 2.5.6 3.6.1.3 0 .7-.2 1z"/></svg>
          (253) 617-4930
        </li>
        <li>
          <svg viewBox="0 0 24 24"><path d="M2 5h20v14H2z M2 5l10 8 10-8" /></svg>
          martin@plumlinegroup.com
        </li>
        <li>
          <svg viewBox="0 0 24 24"><circle cx="12" cy="12" r="10"/><path d="M2 12h20M12 2c3 3 3 17 0 20M12 2c-3 3-3 17 0 20" stroke="#fff" stroke-width="1.5" fill="none"/></svg>
          www.varkoworks.com
        </li>
      </ul>
    </div>

    <div class="divider"></div>
    <p class="address">18761 52nd Avenue S, Marrow Falls, OR 98047</p>

    <svg class="edge-band" viewBox="0 0 520 20" preserveAspectRatio="none" aria-hidden="true">
      <polygon points="0,14 410,0 402,20 0,20" fill="var(--red)"/>
      <polygon points="412,0 432,0 414,20 404,20" fill="var(--navy)"/>
    </svg>
  </section>

</main>
</body>
</html>
```